Tolbek cards

I want a simple business card that pops.
Logo on one side.
On side two i want.
"Are you thinking about a new building on your property, or renovating an existing structure? Contact".....
Owners Name: Dale Whitacre
Owners Phone number: 610-555-0187
Address:4076 Copper Ridge RD, Alder Falls, PA 16910
Committed to Quality, Service, and Integrity

```html
<!DOCTYPE html>
<html lang="en">
<head>
<meta charset="utf-8">
<title>Tolbek Builders LLC – Business Card</title>
<link rel="stylesheet" href="https://fonts.googleapis.com/css2?family=Archivo:ital,wght@0,400;0,700;0,800;1,700&display=swap">
<style>
  :root {
    --backdrop: #5b5b5b;
    --brown-deep: #553924;
    --brown-mid: #7a5f46;
    --tan-light: #a08a72;
    --paper: #ffffff;
    --ink-light: #ffffff;
  }
  * { box-sizing: border-box; margin: 0; padding: 0; }
  html, body {
    width: 1200px;
    height: 1200px;
    overflow: hidden;
    background: var(--backdrop);
    font-family: "Archivo", Arial, sans-serif;
    color: var(--ink-light);
  }
  .canvas { position: relative; width: 1200px; height: 1200px; }

  .card {
    position: absolute;
    left: 256px;
    width: 688px;
    height: 393px;
    overflow: hidden;
  }

  /* Front: contact side */
  .card--front {
    top: 158px;
    background: linear-gradient(90deg,
      var(--brown-mid) 0%, var(--tan-light) 32%, var(--brown-mid) 52%, var(--brown-deep) 62%);
  }
  .brand-art {
    position: absolute;
    top: 0;
    right: 0;
    width: 452px;
    height: 100%;
    background: linear-gradient(135deg, var(--paper) 0%, var(--paper) 30%, var(--tan-light) 65%, var(--brown-deep) 100%);
    clip-path: polygon(35% 100%, 35% 60%, 100% 0, 100% 100%);
  }
  .pitch {
    position: absolute;
    left: 27px;
    top: 28px;
    width: 290px;
    font-size: 20px;
    font-weight: 700;
    font-style: italic;
    line-height: 24px;
  }
  .owner-name {
    position: absolute;
    left: 30px;
    top: 150px;
    font-size: 26px;
    font-weight: 700;
    letter-spacing: 1px;
  }
  .contact {
    position: absolute;
    left: 30px;
    top: 292px;
    font-size: 16px;
    font-weight: 400;
    line-height: 21px;
  }
  .contact__phone { display: flex; align-items: center; gap: 10px; margin-bottom: 11px; }
  .contact__phone svg { width: 14px; height: 14px; fill: var(--ink-light); }

  /* Back: brand side */
  .card--back {
    top: 651px;
    background: radial-gradient(ellipse 60% 75% at 50% 42%, var(--tan-light) 0%, var(--brown-mid) 45%, var(--brown-deep) 100%);
    text-align: center;
  }
  .brand-name {
    position: absolute;
    left: 0;
    right: 0;
    top: 218px;
    font-weight: 800;
    line-height: 1;
  }
  .brand-name__main { display: block; font-size: 72px; letter-spacing: 0; }
  .brand-name__sub { display: block; font-size: 24px; letter-spacing: 3px; margin-top: 6px; }
  .tagline {
    position: absolute;
    left: 0;
    right: 0;
    top: 350px;
    font-size: 18px;
    font-weight: 400;
  }
</style>
</head>
<body>
<main class="canvas">
  <section class="card card--front">
    <div class="brand-art" role="img" aria-label="Large brand mark decoration in brown and white"></div>
    <p class="pitch">Are you thinking about a new building on your property, or renovating an existing structure?</p>
    <h1 class="owner-name">DALE WHITACRE</h1>
    <div class="contact">
      <p class="contact__phone">
        <svg viewBox="0 0 24 24" aria-hidden="true"><path d="M6.6 10.8a15.1 15.1 0 0 0 6.6 6.6l2.2-2.2c.3-.3.7-.4 1-.2 1.1.4 2.3.6 3.6.6.6 0 1 .4 1 1V20c0 .6-.4 1-1 1A17 17 0 0 1 3 4c0-.6.4-1 1-1h3.5c.6 0 1 .4 1 1 0 1.3.2 2.5.6 3.6.1.3 0 .7-.2 1z"/></svg>
        610-555-0187
      </p>
      <p>4076 Copper Ridge RD<br>Alder Falls, PA 16910</p>
    </div>
  </section>

  <section class="card card--back">
    <h2 class="brand-name">
      <span class="brand-name__main">TOLBEK</span>
      <span class="brand-name__sub">BUILDERS LLC</span>
    </h2>
    <p class="tagline">Committed to Quality, Service, and Integrity</p>
  </section>
</main>
</body>
</html>
```